Album art design concept, my band will be releasing a 11 song rock album in the next few Months. We will be using it as a CD cover, poster, online art cover, maybe even Vinyl. Working album titles are "Woven from static" (Preferred album title) or "The river under the stone". Anything abstract, painting-like design, or whatever type of design that comes to mind. Fonts are designers choice. Thank You

Target Market(s)

Music business

Colors

Designer to choose colors to be used in the design.

Requirements
Must have
• Our band logo
Nice to have
• Anything abstract, attractive painting type, maybe even some kind of a futuristic design.
Should not have
• Skulls, blood-like, scary designs, nudity, emo type of design

```html
<!DOCTYPE html>
<html lang="en">
<head>
<meta charset="utf-8">
<title>Woven from static — Cobalt Harbor</title>
<link rel="stylesheet" href="https://fonts.googleapis.com/css2?family=Big+Shoulders+Display:wght@100&family=Josefin+Sans:wght@100&display=swap">
<style>
  :root {
    --rose: #cf9aa3;
    --rose-deep: #c58a98;
    --lilac: #c9b2d8;
    --lavender: #bfaee0;
    --violet-haze: #9a86d6;
    --ink: #141216;
    --stone-dark: #0f3a3a;
    --stone-teal: #2f7d78;
    --stone-gold: #c9a94a;
    --shadow: rgba(40, 30, 50, 0.55);
  }
  * { margin: 0; padding: 0; box-sizing: border-box; }
  html, body { width: 1200px; height: 1200px; overflow: hidden; }
  body { background: var(--lilac); }
  .cover { position: relative; width: 1200px; height: 1200px; }
  .cover__art { position: absolute; inset: 0; width: 1200px; height: 1200px; display: block; }
  .cover__title {
    font-family: "Big Shoulders Display", "Antonio", sans-serif;
    font-weight: 100;
    font-size: 62px;
    fill: var(--ink);
  }
  .cover__band {
    font-family: "Josefin Sans", "Jost", sans-serif;
    font-weight: 100;
    font-size: 74px;
    fill: var(--ink);
  }
</style>
</head>
<body>
<main class="cover">
  <svg class="cover__art" viewBox="0 0 1200 1200" xmlns="http://www.w3.org/2000/svg">
    <defs>
      <linearGradient id="backdrop" x1="0" y1="0" x2="0" y2="1">
        <stop offset="0" stop-color="var(--rose)"/>
        <stop offset="0.35" stop-color="var(--rose-deep)"/>
        <stop offset="0.7" stop-color="var(--lilac)"/>
        <stop offset="1" stop-color="var(--lavender)"/>
      </linearGradient>
      <radialGradient id="haze">
        <stop offset="0" stop-color="var(--violet-haze)" stop-opacity="0.7"/>
        <stop offset="1" stop-color="var(--violet-haze)" stop-opacity="0"/>
      </radialGradient>
      <linearGradient id="stone" x1="0" y1="0" x2="1" y2="1">
        <stop offset="0" stop-color="var(--stone-teal)"/>
        <stop offset="0.45" stop-color="var(--stone-dark)"/>
        <stop offset="0.7" stop-color="var(--stone-gold)" stop-opacity="0.85"/>
        <stop offset="1" stop-color="var(--stone-dark)"/>
      </linearGradient>
      <radialGradient id="floor-shadow">
        <stop offset="0" stop-color="var(--shadow)"/>
        <stop offset="1" stop-color="var(--shadow)" stop-opacity="0"/>
      </radialGradient>
    </defs>

    <rect class="backdrop" width="1200" height="1200" fill="url(#backdrop)"/>
    <g class="backdrop-haze">
      <ellipse cx="110" cy="520" rx="230" ry="110" fill="url(#haze)"/>
      <ellipse cx="1090" cy="520" rx="230" ry="110" fill="url(#haze)"/>
      <ellipse cx="600" cy="220" rx="120" ry="60" fill="url(#haze)"/>
      <ellipse cx="600" cy="1150" rx="260" ry="70" fill="url(#haze)" opacity="0.6"/>
    </g>

    <text class="cover__title" x="600" y="160" text-anchor="middle"
          textLength="592" lengthAdjust="spacing">WOVEN FROM STATIC</text>

    <ellipse class="floor-shadow" cx="612" cy="1002" rx="140" ry="22" fill="url(#floor-shadow)"/>

    <g class="sculpture" role="img" aria-label="Split classical bust in teal and gold marbled stone, floating">
      <path class="sculpture__upper" fill="url(#stone)"
            d="M370 470 C360 380 400 300 470 260 C520 225 560 215 600 212 C680 210 760 250 800 320 C825 365 825 420 815 470 L812 548 C740 550 640 560 540 535 C470 515 410 505 372 500 Z"/>
      <path class="sculpture__lower" fill="url(#stone)"
            d="M402 568 C480 560 600 566 764 600 L752 640 C740 700 722 760 712 820 L712 958 L470 958 C460 900 445 850 430 800 C415 730 405 650 402 568 Z"/>
    </g>

    <text class="cover__band" x="602" y="1127" text-anchor="middle"
          textLength="612" lengthAdjust="spacing">COBALT HARBOR</text>
  </svg>
</main>
</body>
</html>
```